Doctor Formulated Medical Cosmetics

Velour Skinhaus is an E-commerce site for high end Medical Cosmetics designed to treat specific skin problems. The Velour Skinhaus difference/advantage is that all creams and serums are:
Doctor Formulated, Freshly Handmade, Registered Pharmacy.
The Site also provides real doctor Dermatology Consultations, Library (with a list of - 1. Active Ingredients in the creams with description of their effects, 2. Skin Conditions with information on what causes the condition and typical treatment approaches and outcomes. 3. Resources from Dermatology Journals and literature on the conditions.)
Header Information: Velour Skinhaus, languages EN, BG, Register / log in, Shopping Bag. This field should be narrow.
Categories (horizontal): Home, Face, Body, Hair Care, Skin Conditions, Doctor Consultation, Library
The Landing Page should have only one well organized picture, which is intended to create the feeling of luxury, freedom and relaxation. It will be large and will fill the whole screen. All text should be on transparent or similar color fields. Please use the color of the text to create also the feeling of conservative luxury.
Written message / image overlay Velour Skinhaus(logo), Skin Care, Doctor Formulated, Freshly Handmade, Registered Pharmacy.
Please study the Landing Page of this site as an example: www.marivane.com
Under the Landing Page, there should be a slider with 4 of our products.
Underneath: Four Blog Articles (large pictures for maximum impact and luxury text underneath).
Underneath: Banner for Dermatologist Consultation, (button for Start Your Case Now).
Underneath: Two pictures in a line - Library (with books), and Active Ingredients.
Footer: Philosophy, Categories, Customer Care
Please adhere to the color palate provided in the pictures (as attachments). Provided are some examples of Web Sites with the desired look and feel. www.quillora.com , www.tavenholtmd.com .
Please use different shades of gray, white, beige and gold colors, and black. Our products will be in brown glass jars and bottles to convey the professional, pharmacy made nature of the creams and lotions.
We find the following Front Page very attractive and effective - www.marivane.com , with its full page image and overlaying text.
Please have a look at this link for the Landing page.
http://www.brimlensphoto.com/detail/video/woman-lying-on-a-black-sand-beach-in-a-bikini-stock-footage/58213067
I would like to use it in the animated version to achieve the WOW effect. I have uploaded the jpeg version for it, so you will be able create your design.
For the Landing page design, please use only the two uploaded pictures of a woman laying at the beach. Let's see how each of them will look like.
Thank you for your help.

```html
<!DOCTYPE html>
<html lang="en">
<head>
<meta charset="utf-8">
<title>Velour Skinhaus — Doctor Formulated Medical Cosmetics</title>
<link rel="stylesheet" href="https://fonts.googleapis.com/css2?family=Roboto+Slab:wght@400;700&family=Roboto:wght@400;500;700&display=swap">
<style>
:root{
  --gold:#c8a664;
  --gold-dark:#a98a4c;
  --gold-light:#e4cf9f;
  --ink:#222222;
  --ink-soft:#555555;
  --grey-bg:#f0efed;
  --line:#dddddd;
  --white:#ffffff;
  --footer:#2b2b2b;
  --footer-deep:#1f1f1f;
}
*{box-sizing:border-box;margin:0;padding:0}
html,body{width:1200px;height:3236px;overflow:hidden}
body{font-family:"Roboto",Arial,sans-serif;color:var(--ink);background:var(--white);position:relative}
.brand{display:flex;align-items:center;font-family:"Roboto Slab",Georgia,serif;font-weight:400;color:var(--gold);white-space:nowrap}

/* header */
.topbar{position:absolute;left:0;top:0;width:1200px;height:128px;display:flex;align-items:center;justify-content:space-between;padding:0 88px}
.topbar .brand{font-size:34px}
.top-tools{display:flex;align-items:center;gap:18px;font-size:15px;color:var(--ink)}
.lang{display:flex;align-items:center;gap:6px;border:1px solid var(--line);padding:4px 8px}
.flag{width:20px;height:13px;background:linear-gradient(#21468b 0 33%,#fff 33% 66%,#c8102e 66%)}
.btn{display:inline-block;font-size:12px;font-weight:700;letter-spacing:.5px;text-transform:uppercase;padding:9px 18px;color:var(--white)}
.btn-gold{background:var(--gold)}
.btn-dark{background:var(--ink)}
.nav{position:absolute;left:0;top:128px;width:1200px;height:48px;background:var(--gold);padding:0 88px;display:flex;align-items:stretch}
.nav a{color:var(--white);text-decoration:none;font-size:13px;font-weight:500;text-transform:uppercase;padding:0 17px;display:flex;align-items:center}
.nav a.active{background:var(--gold-dark)}

/* hero */
.hero{position:absolute;left:0;top:176px;width:1200px;height:424px;overflow:hidden}
.hero-photo{position:absolute;inset:0;background:linear-gradient(90deg,#2c2620 0%,#4a3c2e 38%,#8a6a44 62%,#c9a06a 80%,#e2c89c 100%)}
.hero-text{position:absolute;left:88px;top:52px;color:var(--white)}
.hero-text .brand{color:var(--white);font-size:40px;margin-bottom:40px}
.hero-text h1{font-family:"Roboto Slab",Georgia,serif;font-weight:400;font-size:26px;line-height:38px;max-width:430px}
.dots{position:absolute;left:88px;top:368px;display:flex;gap:8px}
.dots span{width:12px;height:12px;border-radius:50%;border:2px solid var(--white)}
.dots span.on{background:var(--white)}

/* section titles */
.sec-title{display:flex;align-items:center;justify-content:center;gap:22px}
.sec-title .rule{width:90px;height:1px;background:var(--gold)}
.sec-title h2{font-family:"Roboto Slab",Georgia,serif;font-weight:400;font-size:30px;color:var(--gold);white-space:nowrap}
.on-gold .rule{background:var(--white)}
.on-gold h2{color:var(--white)}

/* products */
.products{position:absolute;left:0;top:600px;width:1200px;height:560px}
.products .sec-title{position:absolute;left:0;right:0;top:120px}
.product-row{position:absolute;left:208px;top:220px;display:flex;gap:16px}
.product{width:212px;height:290px;border:1px solid var(--line);background:var(--white);box-shadow:0 2px 6px rgba(0,0,0,.08);padding:12px}
.product-img{height:150px;background:linear-gradient(180deg,#f6f3ee,#e6dccb)}
.product h3{font-size:16px;font-weight:700;text-align:center;margin-top:14px}
.product p{font-size:12px;color:var(--ink-soft);text-align:center;margin-top:6px}
.product .buy{display:flex;justify-content:space-between;align-items:center;margin-top:18px;font-size:14px;font-weight:700}
.product .buy .btn{font-size:11px;padding:7px 12px;text-transform:none;font-weight:500}

/* blog */
.blog{position:absolute;left:0;top:1160px;width:1200px;height:740px;background:var(--gold)}
.blog .sec-title{position:absolute;left:0;right:0;top:42px}
.blog-grid{position:absolute;left:8px;top:130px;display:grid;grid-template-columns:588px 588px;grid-template-rows:292px 292px;gap:8px}
.blog-card{position:relative;overflow:hidden}
.blog-card .photo{position:absolute;inset:0}
.blog-card .cap{position:absolute;left:24px;bottom:22px;color:var(--white)}
.blog-card .cap h3{font-size:17px;font-weight:700}
.blog-card .cap p{font-size:13px;margin-top:4px;opacity:.9}
.p1{background:linear-gradient(135deg,#3d3128,#7b6451 55%,#a58a70)}
.p2{background:linear-gradient(135deg,#6c6e70,#9a9896 55%,#c9c2b6)}
.p3{background:linear-gradient(135deg,#2e4152,#55707f 55%,#9c8b78)}
.p4{background:linear-gradient(135deg,#294a3d,#4f8066 55%,#9db59b)}

/* consultation */
.consult{position:absolute;left:0;top:1900px;width:1200px;height:420px;background:linear-gradient(90deg,#ffffff,#ecebe8 70%)}
.consult-text{position:absolute;left:150px;top:64px;width:460px;text-align:center}
.consult-text .brand{justify-content:center;font-size:30px}
.consult-text h2{font-family:"Roboto Slab",Georgia,serif;font-weight:400;font-size:26px;color:var(--gold);margin-top:28px}
.consult-text p{font-size:13px;line-height:20px;color:var(--ink-soft);margin-top:16px}
.consult-text .btn{margin-top:22px}
.consult-photo{position:absolute;right:0;top:0;width:420px;height:420px;background:linear-gradient(120deg,#ebe8e3,#c9a27c 55%,#8a5f3f)}

/* articles */
.articles{position:absolute;left:0;top:2320px;width:1200px;height:580px}
.articles .sec-title{position:absolute;left:0;right:0;top:44px}
.article-row{position:absolute;left:128px;top:124px;display:flex;gap:18px}
.article{width:230px;height:420px;background:var(--white);border:1px solid var(--line);box-shadow:0 2px 6px rgba(0,0,0,.08);text-align:center}
.article .photo{height:170px}
.a1{background:linear-gradient(135deg,#4a3a30,#9b7d66)}
.a2{background:linear-gradient(135deg,#e2cdb3,#b7906c)}
.a3{background:linear-gradient(135deg,#2f3640,#6e7680)}
.a4{background:linear-gradient(135deg,#d9c49f,#9c7c55)}
.article h3{font-size:14px;font-weight:700;margin-top:20px}
.article h3.gold{color:var(--gold)}
.article p{font-size:12px;line-height:18px;color:var(--ink-soft);padding:10px 18px 0;height:92px}
.btn-line{display:inline-block;font-size:12px;padding:8px 16px;border:1px solid var(--ink);color:var(--ink);margin-top:18px}
.btn-fill{display:inline-block;font-size:12px;padding:8px 16px;border:1px solid var(--gold);background:var(--gold);color:var(--white);margin-top:18px}

/* footer */
.footer{position:absolute;left:0;top:2900px;width:1200px;height:300px;background:var(--footer);color:#cfcfcf;font-size:13px}
.footer .brand{position:absolute;left:88px;top:60px;font-size:32px;color:var(--white)}
.socials{position:absolute;left:88px;top:132px;display:flex;gap:8px}
.socials span{width:26px;height:26px;border-radius:50%;border:1px solid #cfcfcf}
.fcol{position:absolute;top:40px}
.fcol h4{color:var(--white);font-size:14px;font-weight:700;text-transform:uppercase;margin-bottom:18px}
.fcol li{list-style:none;margin-bottom:10px}
.fcol li::before{content:"›";margin-right:8px;color:var(--gold)}
.contact-item{display:flex;gap:10px;margin-bottom:16px;line-height:18px}
.contact-item svg{flex:none;margin-top:2px}
.contact-item b{color:var(--white);font-weight:500}
.form-row{display:flex;gap:8px;margin-bottom:8px}
.field{height:30px;border:1px solid #555;background:#333;color:#999;font-size:12px;padding:7px 8px;flex:1}
.field.tall{height:80px}
.footer .btn{margin-top:6px;font-size:11px}
.copy{position:absolute;left:0;top:3200px;width:1200px;height:36px;background:var(--footer-deep);color:#999;font-size:12px;display:flex;align-items:center;justify-content:center;border-top:2px solid var(--gold)}
</style>
</head>
<body>

<header class="topbar">
  <div class="brand">Velour Skinhaus</div>
  <div class="top-tools">
    <span class="lang"><span class="flag"></span>Eng ▾</span>
    <span>Doctor</span><span>|</span><span>Pharmacy</span>
    <svg width="20" height="22" viewBox="0 0 20 22" aria-label="Shopping bag"><path d="M3 7h14l-1 14H4z" fill="var(--gold)"/><path d="M7 8V5a3 3 0 0 1 6 0v3" fill="none" stroke="var(--gold)" stroke-width="1.6"/></svg>
    <span class="btn btn-gold">Register</span>
    <span class="btn btn-dark">Login</span>
  </div>
</header>

<nav class="nav">
  <a class="active">Home</a><a>Face</a><a>Body</a><a>Hair Care</a><a>Skin Concerns</a><a>Dermatologist Consultation</a><a>Library</a><a>Contact Us</a>
</nav>

<section class="hero">
  <div class="hero-photo" role="img" aria-label="Woman with flowing golden hair, eyes closed, relaxed luxury mood"></div>
  <div class="hero-text">
    <div class="brand">Velour Skinhaus</div>
    <h1>Doctor Formulated, Freshly Hand made, Registered Pharmacy, Highest Ethical Standards</h1>
  </div>
  <div class="dots"><span class="on"></span><span></span><span></span><span></span><span></span></div>
</section>

<section class="products">
  <div class="sec-title"><span class="rule"></span><h2>Velour Skinhaus Products</h2><span class="rule"></span></div>
  <div class="product-row">
    <div class="product"><div class="product-img" role="img" aria-label="White skincare bottles and jars"></div><h3>Product Name</h3><p>Gentle daily repair cream</p><div class="buy"><span>$55.00</span><span class="btn btn-gold">Add to Cart</span></div></div>
    <div class="product"><div class="product-img" role="img" aria-label="Skincare bottles with teal caps"></div><h3>Product Name</h3><p>Calming serum for redness</p><div class="buy"><span>$55.00</span><span class="btn btn-dark">Add to Cart</span></div></div>
    <div class="product"><div class="product-img" role="img" aria-label="Gold and white cosmetic tubes"></div><h3>Product Name</h3><p>Rich night renewal balm</p><div class="buy"><span>$55.00</span><span class="btn btn-dark">Add to Cart</span></div></div>
    <div class="product"><div class="product-img" role="img" aria-label="Skincare pump bottles and jars"></div><h3>Product Name</h3><p>Light hydrating day fluid</p><div class="buy"><span>$55.00</span><span class="btn btn-dark">Add to Cart</span></div></div>
  </div>
</section>

<section class="blog">
  <div class="sec-title on-gold"><span class="rule"></span><h2>Our Blog Articles</h2><span class="rule"></span></div>
  <div class="blog-grid">
    <article class="blog-card"><div class="photo p1" role="img" aria-label="Woman with wavy hair in warm light"></div><div class="cap"><h3>Secrets of radiant skin</h3><p>Read the latest from our doctors</p></div></article>
    <article class="blog-card"><div class="photo p2" role="img" aria-label="Blonde woman against a grey wall"></div><div class="cap"><h3>Caring for sensitive skin</h3><p>Simple steps for every season</p></div></article>
    <article class="blog-card"><div class="photo p3" role="img" aria-label="Woman in a city street scene"></div><div class="cap"><h3>Protecting skin in town</h3><p>How pollution affects your face</p></div></article>
    <article class="blog-card"><div class="photo p4" role="img" aria-label="Woman in sunglasses by green glass facade"></div><div class="cap"><h3>Summer sun and you</h3><p>Choosing the right daily shield</p></div></article>
  </div>
</section>

<section class="consult">
  <div class="consult-text">
    <div class="brand">Velour Skinhaus</div>
    <h2>Dermatologist Consultation</h2>
    <p>Speak with a registered dermatologist about your skin concern and receive a personal treatment plan made for you in our own pharmacy.</p>
    <span class="btn btn-dark">Read More</span>
  </div>
  <div class="consult-photo" role="img" aria-label="Smiling woman with glowing skin"></div>
</section>

<section class="articles">
  <div class="sec-title"><span class="rule"></span><h2>Velour Skinhaus Articles</h2><span class="rule"></span></div>
  <div class="article-row">
    <article class="article"><div class="photo a1" role="img" aria-label="Portrait of a dark haired woman"></div><h3>NEMO ENIM IPSAM</h3><p>Understanding the causes of adult acne and the treatments that bring calm lasting results.</p><span class="btn-line">Read More</span></article>
    <article class="article"><div class="photo a2" role="img" aria-label="Woman with soft auburn hair"></div><h3 class="gold">NEMO ENIM IPSAM</h3><p>Active ingredients explained, from retinol to niacinamide, and what each one does for you.</p><span class="btn-fill">Read More</span></article>
    <article class="article"><div class="photo a3" role="img" aria-label="Woman in dark clothing"></div><h3>NEMO ENIM IPSAM</h3><p>Rosacea and redness, the common triggers and the gentle care that helps skin settle.</p><span class="btn-line">Read More</span></article>
    <article class="article"><div class="photo a4" role="img" aria-label="Woman with light blonde hair"></div><h3>NEMO ENIM IPSAM</h3><p>What recent dermatology journals say about ageing skin and the routines that truly work.</p><span class="btn-line">Read More</span></article>
  </div>
</section>

<footer class="footer">
  <div class="brand">Velour Skinhaus</div>
  <div class="socials"><span></span><span></span><span></span><span></span><span></span><span></span></div>

  <div class="fcol" style="left:384px">
    <h4>Quick Links</h4>
    <ul><li>Home</li><li>Team</li><li>Programs</li><li>Blog</li><li>Our Story</li><li>Contact</li></ul>
  </div>

  <div class="fcol" style="left:560px;width:200px">
    <h4>Contact Us</h4>
    <div class="contact-item"><svg width="12" height="16" viewBox="0 0 12 16"><path d="M6 0a6 6 0 0 1 6 6c0 4-6 10-6 10S0 10 0 6a6 6 0 0 1 6-6z" fill="var(--gold)"/><circle cx="6" cy="6" r="2" fill="var(--footer)"/></svg><div><b>Velour Skinhaus</b><br>12 Linden Row,<br>Sofia 1000</div></div>
    <div class="contact-item"><svg width="14" height="14" viewBox="0 0 14 14"><path d="M3 0l3 3-2 2c1 2 3 4 5 5l2-2 3 3-2 3C6 14 0 8 0 3z" fill="var(--gold)"/></svg><div><b>Phone</b><br>+359 2 555 0134</div></div>
    <div class="contact-item"><svg width="16" height="12" viewBox="0 0 16 12"><rect width="16" height="12" fill="var(--gold)"/><path d="M0 0l8 7 8-7" fill="none" stroke="var(--footer)" stroke-width="1.4"/></svg><div><b>Email</b><br>care@velourskinhaus.com</div></div>
  </div>

  <div class="fcol" style="left:812px;width:300px">
    <h4>Contact Form</h4>
    <div class="form-row"><span class="field">Name</span><span class="field">Phone</span></div>
    <div class="form-row"><span class="field">Email</span></div>
    <div class="form-row"><span class="field tall">Message</span></div>
    <span class="btn btn-gold">Send Message</span>
  </div>
</footer>
<div class="copy">Copyright © 2016 Velour Skinhaus. All Rights Reserved.</div>

</body>
</html>
```